Diverse, up-scale salon needs eye-catching, unique business cards.

We are looking for a unique business card design for our stylist but that can also be multi functional and used for appointment reminder and referrals. I will need a design in a format that I can modify names and titles going forward. In the past we have had a dark background with the logo on one side, and stylist and contact information on the other but we are open to all ideas. I have included our mission statement as well as branded colors below. The statement doesn't need to go on the card, it's just a reference for target market. We need space for the stylists name, title, instagram handle and then the salons phone number, website and address. I am also open to adding a spot for a qr code linked to the stylist instagram or the salon booking link.

primary brand colors:
#333333 #233415 #36502a #93874a #000000
Mission statement:
Vessolin Hair Studio, a high-end salon located in the lively Downtown Farmington, Michigan, is committed to providing exceptional services in a welcoming and relaxed environment to meet the needs of our diverse clientele.
Our salon specializes in contemporary custom haircuts, coloring, extensions, and barbering and beard grooming services. Our team of skilled stylists is passionate and inventive in their hair styling techniques. At the heart of our salon are values centered on quality, innovation, creativity, and above all, comfort. These core values are evident in every appointment across our customizable array of services.
Our goal is to establish a benchmark for exceptional hair care for every human.
Website: www.vessolinhairstudio.example
instagram: @vessolinhairstudio
address: 41782 Pelham Crest Rd, Brackenford NV
phone: 555-613-4087

Industry/Entity Type

Hair Salon

Contact Information for Business Card

Stylist name, title, phone, instagram, website, address, (optional qr code)

Requirements
Should not have
• Does not need mission statement on the card.

```html
<!DOCTYPE html>
<html lang="en">
<head>
<meta charset="utf-8">
<title>Vessolin Hair Studio – Stylist Business Card</title>
<link rel="stylesheet" href="https://fonts.googleapis.com/css2?family=Poppins:wght@400;500;600;700&family=Kaushan+Script&display=swap">
<style>
  :root {
    --stage: #cdcdcd;
    --ink: #111111;
    --card-dark: #1b1b1b;
    --card-dark-soft: #262626;
    --paper: #ffffff;
    --gold: #b39f55;
    --gold-light: #d2bf73;
    --gold-deep: #93874a;
    --text-dark: #141414;
  }
  * { margin: 0; padding: 0; box-sizing: border-box; }
  html, body { width: 1200px; height: 900px; overflow: hidden; }
  body {
    background: var(--stage);
    font-family: "Poppins", sans-serif;
    position: relative;
  }

  .card {
    position: absolute;
    width: 345px;
    height: 604px;
    overflow: hidden;
  }
  .card--front { left: 245px; top: 94px; background: var(--paper); }
  .card--back { left: 634px; top: 209px; }

  .photo-area {
    position: absolute;
    inset: 0;
    background: radial-gradient(ellipse at 60% 40%, var(--card-dark-soft) 0%, var(--card-dark) 65%, #141414 100%);
  }
  .card--front .header {
    position: absolute;
    left: 0; top: 0;
    width: 345px; height: 243px;
  }

  .brand-mark {
    position: absolute;
    display: flex;
    flex-direction: column;
    align-items: center;
    color: var(--gold);
    font-family: "Poppins", sans-serif;
    font-weight: 600;
    text-transform: uppercase;
    text-align: center;
  }
  .brand-mark__circle {
    border: 2px solid var(--gold);
    border-radius: 50%;
  }
  .header .brand-mark { left: 0; width: 345px; top: 36px; }
  .header .brand-mark__circle { width: 62px; height: 62px; }
  .header .brand-mark__name { margin-top: 8px; font-size: 10px; letter-spacing: 2px; }

  .stylist-name {
    position: absolute;
    left: 0; width: 345px; top: 134px;
    text-align: center;
    white-space: nowrap;
    line-height: 1;
  }
  .stylist-name__first {
    font-family: "Poppins", sans-serif;
    font-weight: 400;
    font-size: 38px;
    color: var(--gold);
  }
  .stylist-name__last {
    font-family: "Kaushan Script", cursive;
    font-size: 36px;
    color: var(--paper);
    margin-left: 4px;
  }
  .stylist-studio {
    position: absolute;
    left: 0; width: 345px; top: 190px;
    text-align: center;
    font-size: 11.5px;
    font-weight: 500;
    letter-spacing: 3px;
    color: var(--gold);
  }

  .contact-item {
    position: absolute;
    left: 0; width: 345px;
    text-align: center;
    color: var(--text-dark);
    font-size: 18px;
    font-weight: 400;
    line-height: 1.25;
  }
  .contact-item svg { display: block; margin: 0 auto 3px; }
  .contact-item--phone { top: 282px; }
  .contact-item--address { top: 352px; }
  .contact-item--social { top: 446px; }

  .web-pill {
    position: absolute;
    height: 25px;
    border-radius: 13px;
    display: flex;
    align-items: center;
    justify-content: center;
    font-size: 11px;
    font-weight: 700;
    letter-spacing: 1.6px;
    white-space: nowrap;
  }
  .card--front .web-pill {
    left: 38px; top: 532px; width: 271px;
    background: linear-gradient(90deg, var(--gold-deep), var(--gold-light) 55%, var(--gold-deep));
    color: var(--ink);
  }
  .card--back .web-pill {
    left: 37px; top: 533px; width: 271px;
    border: 1px solid #8a8a8a;
    color: var(--gold);
  }

  .card--back .brand-mark { left: 0; width: 345px; top: 220px; }
  .card--back .brand-mark__circle { width: 150px; height: 150px; border-width: 3px; }
  .card--back .brand-mark__name { margin-top: 14px; font-size: 15px; letter-spacing: 3px; }
</style>
</head>
<body>

  <section class="card card--front" aria-label="Business card front">
    <div class="header">
      <div class="photo-area" role="img" aria-label="Dark monochrome photo of a stylist cutting a client's hair"></div>
      <div class="brand-mark">
        <div class="brand-mark__circle"></div>
        <div class="brand-mark__name">Vessolin Hair Studio</div>
      </div>
      <h1 class="stylist-name">
        <span class="stylist-name__first">Renata</span><span class="stylist-name__last">Colville</span>
      </h1>
      <p class="stylist-studio">VESSOLIN HAIR STUDIO</p>
    </div>

    <div class="contact-item contact-item--phone">
      <svg width="18" height="18" viewBox="0 0 24 24" aria-hidden="true">
        <path fill="#b39f55" d="M6.6 10.8a15.1 15.1 0 0 0 6.6 6.6l2.2-2.2a1 1 0 0 1 1-.25 11.4 11.4 0 0 0 3.6.57 1 1 0 0 1 1 1V20a1 1 0 0 1-1 1A17 17 0 0 1 3 4a1 1 0 0 1 1-1h3.5a1 1 0 0 1 1 1c0 1.25.2 2.45.57 3.6a1 1 0 0 1-.25 1z"/>
      </svg>
      555-613-4087
    </div>

    <div class="contact-item contact-item--address">
      <svg width="18" height="22" viewBox="0 0 24 30" aria-hidden="true">
        <path fill="#b39f55" d="M12 0C5.4 0 0 5.2 0 11.7 0 20 12 30 12 30s12-10 12-18.3C24 5.2 18.6 0 12 0zm0 16a4.5 4.5 0 1 1 0-9 4.5 4.5 0 0 1 0 9z"/>
      </svg>
      41782 Pelham Crest Rd,<br>Brackenford NV
    </div>

    <div class="contact-item contact-item--social">
      <svg width="20" height="14" viewBox="0 0 24 16" aria-hidden="true">
        <rect x="0.5" y="0.5" width="23" height="15" fill="#b39f55"/>
        <path d="M1 1l11 8 11-8M1 15l8-7M23 15l-8-7" stroke="#ffffff" stroke-width="1.4" fill="none"/>
      </svg>
      @vessolinhairstudio
    </div>

    <div class="web-pill">www.vessolinhairstudio.example</div>
  </section>

  <section class="card card--back" aria-label="Business card back">
    <div class="photo-area" role="img" aria-label="Dark monochrome photo of a barber trimming a client's hair with scissors"></div>
    <div class="brand-mark">
      <div class="brand-mark__circle"></div>
      <div class="brand-mark__name">Vessolin Hair Studio</div>
    </div>
    <div class="web-pill">www.vessolinhairstudio.example</div>
  </section>

</body>
</html>
```